Revamp of existing namecard

Existingly, i've got a namecard that i would like to retain the main design. but there are some changes in my company and i would need to do some amendments to it.

We are a money transfer and money exchange company.
I need 2 different types of name card.
1. For individual name cards
the front to put the following:
Company name and logo
English Name, Chinese Name appointment
Mobile Number, Email and Website.
2 License number under the logo and name

the back of the name card to put
8 address: 7 Singapore and 1 Hong Kong branch addresses
8 Mobile Number of the corresponding addresses.

We would like to retain the name card front design
the name card back design can change but color to retain.

2nd name card is generic name card
Front:
Company name and logo
Branch Mobile Number, Branch Address, Email and Website.

Industry/Entity Type

remittance and money exchange

Contact Information for Business Card

I need 2 different types of name card. 1. For individual name cards the front to put the following: Company name and logo English Name, Chinese Name appointment Mobile Number, Email and Website. 2 License number under the logo and name the back of the name card to put 8 address: 7 Singapore and 1 Hong Kong branch addresses 8 Mobile Number of the corresponding addresses. We would like to retain the name card front design the name card back design can change but color to retain. 2nd name card is generic name card Front: the front to put the following: Company name and logo Branch Mobile Number, Branch Address, Email and Website. 2 License number under the logo and name

Requirements
Must have
• I need 2 different types of name card. 1. For individual name cards the front to put the following: Company name and logo English Name, Chinese Name appointment Mobile Number, Email and Website. 2 License number under the logo and name the back of the name card to put 8 address: 7 Singapore and 1 Hong Kong branch addresses 8 Mobile Number of the corresponding addresses. We would like to retain the name card front design the name card back design can change but color to retain. 2nd name card is generic name card Front: the front to put the following: Company name and logo Branch Mobile Number, Branch Address, Email and Website. 2 License number under the logo and name
Nice to have
• use back color code

```html
<!DOCTYPE html>
<html lang="en">
<head>
<meta charset="utf-8">
<title>Corvane Business Card</title>
<link rel="stylesheet" href="https://fonts.googleapis.com/css2?family=Montserrat:wght@400;500;700&display=swap">
<style>
  :root {
    --backdrop: #ebecee;
    --card: #ffffff;
    --ink: #1e1e1e;
    --ink-soft: #333333;
    --teal: #3a9fb5;
    --map-light: #f1f1f1;
    --map-dark: #d9d9d9;
  }
  * { margin: 0; padding: 0; box-sizing: border-box; }
  html, body {
    width: 1200px;
    height: 1033px;
    overflow: hidden;
    background: var(--backdrop);
    font-family: "Montserrat", sans-serif;
    color: var(--ink);
  }
  .business-card {
    position: absolute;
    left: 100px;
    top: 211px;
    width: 1000px;
    height: 610px;
    background: var(--card);
    box-shadow: 0 6px 24px rgba(0, 0, 0, 0.10);
    overflow: hidden;
  }
  .world-map {
    position: absolute;
    left: 35px;
    top: 63px;
    width: 945px;
    height: 465px;
    border-radius: 40px;
    background: radial-gradient(ellipse at 55% 45%, var(--map-dark) 0%, var(--map-light) 60%, rgba(255,255,255,0) 100%);
    opacity: 0.85;
  }
  .brand {
    position: absolute;
    left: 520px;
    top: 88px;
    display: flex;
    align-items: center;
    gap: 18px;
  }
  .brand-mark {
    width: 58px;
    height: 58px;
    border-radius: 50%;
    background: var(--teal);
    flex: none;
  }
  .brand-text { display: flex; flex-direction: column; }
  .brand-name {
    font-size: 64px;
    font-weight: 500;
    letter-spacing: 3px;
    line-height: 1;
    color: var(--ink);
  }
  .brand-licence {
    margin-top: 4px;
    margin-left: 42px;
    font-size: 22px;
    font-weight: 700;
    letter-spacing: 1.5px;
    color: var(--ink);
  }
  .branch {
    position: absolute;
    left: 42px;
    top: 228px;
    display: flex;
    align-items: flex-start;
    gap: 10px;
  }
  .branch-pin { width: 40px; height: 54px; margin-top: 6px; }
  .branch-name {
    font-size: 52px;
    font-weight: 700;
    line-height: 1.1;
    color: var(--ink);
  }
  .branch-label {
    font-size: 22px;
    font-weight: 400;
    color: var(--teal);
    line-height: 1;
  }
  .address {
    position: absolute;
    left: 62px;
    top: 346px;
    font-size: 24px;
    font-weight: 500;
    line-height: 34px;
    color: var(--ink-soft);
    font-style: normal;
  }
  .contacts {
    position: absolute;
    left: 590px;
    top: 290px;
    list-style: none;
  }
  .contact {
    display: flex;
    align-items: center;
    gap: 12px;
    height: 39px;
    font-size: 25px;
    font-weight: 500;
    letter-spacing: 1px;
    color: var(--ink-soft);
  }
  .contact-icon { width: 24px; height: 24px; flex: none; }
</style>
</head>
<body>
  <main class="business-card">
    <div class="world-map" role="img" aria-label="Faint dotted world map in light grey"></div>

    <header class="brand">
      <span class="brand-mark"></span>
      <div class="brand-text">
        <span class="brand-name">CORVANE</span>
        <span class="brand-licence">04817320 | 04817320</span>
      </div>
    </header>

    <section class="branch">
      <svg class="branch-pin" viewBox="0 0 40 54" aria-hidden="true">
        <path d="M20 2C10 2 2 10 2 20c0 13 18 32 18 32s18-19 18-32C38 10 30 2 20 2z" fill="var(--teal)"/>
        <circle cx="20" cy="20" r="7" fill="#fff"/>
      </svg>
      <div>
        <h1 class="branch-name">Kelvin Quay</h1>
        <p class="branch-label">branch</p>
      </div>
    </section>

    <address class="address">
      Suite 1605, 16th Floor<br>
      Harbour Crest Tower<br>
      48 Lockhart Road, Wan Chai
    </address>

    <ul class="contacts">
      <li class="contact">
        <svg class="contact-icon" viewBox="0 0 24 24" aria-hidden="true">
          <rect x="6" y="1.5" width="12" height="21" rx="2" fill="none" stroke="var(--teal)" stroke-width="2"/>
          <circle cx="12" cy="18.5" r="1.3" fill="var(--teal)"/>
        </svg>
        +852 9431 6278
      </li>
      <li class="contact">
        <svg class="contact-icon" viewBox="0 0 24 24" aria-hidden="true">
          <path d="M6.6 10.8a15 15 0 0 0 6.6 6.6l2.2-2.2c.3-.3.7-.4 1-.2 1.1.4 2.3.6 3.6.6.6 0 1 .4 1 1V20c0 .6-.4 1-1 1A17 17 0 0 1 3 4c0-.6.4-1 1-1h3.5c.6 0 1 .4 1 1 0 1.3.2 2.5.6 3.6.1.3 0 .7-.2 1z" fill="var(--teal)"/>
        </svg>
        +852 9574 38
      </li>
      <li class="contact">
        <svg class="contact-icon" viewBox="0 0 24 24" aria-hidden="true">
          <rect x="2" y="5" width="20" height="14" rx="1.5" fill="var(--teal)"/>
          <path d="M3 6l9 7 9-7" fill="none" stroke="#fff" stroke-width="1.6"/>
        </svg>
        mara@corvane.com.hk
      </li>
      <li class="contact">
        <svg class="contact-icon" viewBox="0 0 24 24" aria-hidden="true">
          <circle cx="12" cy="12" r="10" fill="none" stroke="var(--teal)" stroke-width="1.8"/>
          <ellipse cx="12" cy="12" rx="4.5" ry="10" fill="none" stroke="var(--teal)" stroke-width="1.6"/>
          <path d="M2 12h20M4 7h16M4 17h16" stroke="var(--teal)" stroke-width="1.4"/>
        </svg>
        www.corvane.com.hk
      </li>
    </ul>
  </main>
</body>
</html>
```